Design for the A4 Letterhead, envelope and A4 Folder

Design have to be clean, professional, unique (eye catchy) and high end.
Colors: Yellow (Code: 803C), Darker Grey and Black or white (optional)
Logo can be in white or black

Letterhead:
Contain: 1. Korvane Logo
2. Slogan "MADE WITH PRIDE"
3. Company information:
Korvane Valves Pte. Ltd. (Singapore)
Registration no: 201947215K
Tel: (65) 6418 2904
Fax: (65) 6472 9186
Email: sales@korvanevalves.example
Website: http://www.korvanevalves.example
4. Logo watermark

Envelope:
Contain: 1. Korvane Logo
3. website: http://www.korvanevalves.example and email address:
sales@korvanevalves.example
4. Logo watermark

Folder:
Contain: 1. Korvane Logo
3. Company's information:
Tel: (65) 6418 2904
Fax: (65) 6472 9186
4. QR Code
5. Logo watermark
6. On the inside there is a space to insert business card. Contrast colors
between the inside and cover.
Updates

For the Folder design, please be informed that we would prefer to have the Korvane logo on the left hand side of the cover page, rather than on the right hand side.And also if we could highlight the "Made with Pride" slogan with either the yellow box or black/grey box depending on the background color.For the Envelope design,it does not matter where the position of the logo is. But please also highlight the "Made with Pride" Slogan For the Letterhead design, the position of the logo must be on the left hand side and the slogan must be highlighted. In addition, please include the following company information (only for the letterhead design)Korvane Valves Pte. Ltd. (Singapore)Registration no: 200308878MTel: (65) 6535 3735Fax: (65) 6533 3570Email: sales@dynatechpumps.comWebsite: http://www.korvanevalves.example Added Wednesday, August 2, 2017

Target Market(s)

Business to Business, High End market

Industry/Entity Type

It Professional

Font styles to use
Serif

Requirements
Must have
• Design have to be clean, professional, unique (eye catchy) and high end.
Nice to have
• color contrast but still maintaining the professionalism and the seriousness
Should not have
• Messy look, futuristic look, too crowded

```html
<!DOCTYPE html>
<html lang="en">
<head>
<meta charset="utf-8">
<title>Korvane Valves – Letterhead</title>
<link rel="stylesheet" href="https://fonts.googleapis.com/css2?family=Oswald:wght@400&family=Open+Sans:wght@400;700&display=swap">
<style>
  :root {
    --backdrop: #e6da82;
    --paper: #fdfdf8;
    --brand-yellow: #f5e829;
    --slogan-yellow: #f2e21c;
    --dark-grey: #3f4043;
    --ink: #1c1c1c;
    --muted: #6d6d6d;
    --watermark: #ededea;
  }
  * { box-sizing: border-box; margin: 0; padding: 0; }
  html, body {
    width: 1200px; height: 784px; overflow: hidden;
    background: var(--backdrop);
  }
  .letterhead {
    position: absolute; left: 338px; top: 22px;
    width: 523px; height: 740px;
    background: var(--paper);
    box-shadow: 0 2px 10px rgba(0,0,0,0.12);
    overflow: hidden;
  }
  .edge-bar { position: absolute; }
  .edge-bar--yellow { background: var(--brand-yellow); }
  .edge-bar--dark { background: var(--dark-grey); }

  .brand {
    position: absolute; left: 16px; top: 10px;
    display: flex; flex-direction: column; align-items: flex-start;
  }
  .brand-dot {
    width: 30px; height: 30px; border-radius: 50%;
    background: var(--ink); margin-left: 14px; margin-bottom: 4px;
  }
  .brand-name {
    font-family: "Oswald", sans-serif; font-weight: 400;
    font-size: 20px; line-height: 1; letter-spacing: 0.5px;
    color: var(--ink); text-transform: uppercase;
  }
  .brand-region {
    font-family: "Oswald", sans-serif; font-weight: 400;
    font-size: 6px; letter-spacing: 4.2px; color: var(--ink);
    text-transform: uppercase; margin-top: 2px;
  }

  .contact {
    position: absolute; right: 22px; top: 26px;
    font-family: "Open Sans", sans-serif; font-size: 7.5px;
    line-height: 1.45; color: var(--muted);
    list-style: none;
  }
  .contact-company { font-weight: 700; color: var(--ink); font-size: 8px; }
  .contact li { display: flex; align-items: center; gap: 4px; }
  .contact-icon { width: 6px; height: 6px; border-radius: 50%; background: var(--dark-grey); flex: none; }

  .watermark {
    position: absolute; left: 140px; top: 520px;
  }

  .slogan {
    position: absolute; right: 20px; bottom: 14px;
    font-family: "Oswald", sans-serif; font-weight: 400;
    font-size: 24px; letter-spacing: 1px; line-height: 1;
    color: var(--slogan-yellow); text-transform: uppercase;
  }
</style>
</head>
<body>
  <main class="letterhead">
    <span class="edge-bar edge-bar--yellow" style="left:0;top:4px;width:4px;height:28px"></span>
    <span class="edge-bar edge-bar--dark" style="left:0;top:41px;width:4px;height:40px"></span>

    <span class="edge-bar edge-bar--yellow" style="right:0;top:4px;width:4px;height:34px"></span>
    <span class="edge-bar edge-bar--dark" style="right:0;top:44px;width:4px;height:34px"></span>

    <span class="edge-bar edge-bar--dark" style="left:0;bottom:0;width:131px;height:5px"></span>
    <span class="edge-bar edge-bar--yellow" style="left:131px;bottom:0;width:178px;height:5px"></span>
    <span class="edge-bar edge-bar--dark" style="left:309px;bottom:0;width:214px;height:5px"></span>

    <div class="brand">
      <span class="brand-dot"></span>
      <span class="brand-name">Korvane</span>
      <span class="brand-region">Singapore</span>
    </div>

    <ul class="contact">
      <li class="contact-company">Korvane Valves Pte. Ltd. (Singapore)</li>
      <li><span class="contact-icon"></span>Regd. No. 201947215K</li>
      <li>
        <svg class="contact-glyph" width="7" height="7" viewBox="0 0 10 10" aria-hidden="true"><path d="M2 1h2l1 2.5-1.3 1a5 5 0 0 0 2.8 2.8l1-1.3L10 7v2a1 1 0 0 1-1 1A8 8 0 0 1 1 2a1 1 0 0 1 1-1z" fill="#3f4043"/></svg>
        (65) 6418 2904
      </li>
      <li>
        <svg class="contact-glyph" width="7" height="7" viewBox="0 0 10 10" aria-hidden="true"><rect x="2" y="0.5" width="6" height="3" fill="#3f4043"/><rect x="0.5" y="4" width="9" height="4" fill="#3f4043"/><rect x="2.5" y="7" width="5" height="2.5" fill="#3f4043"/></svg>
        (65) 6472 9186
      </li>
      <li>
        <svg class="contact-glyph" width="7" height="7" viewBox="0 0 10 10" aria-hidden="true"><rect x="0.5" y="2" width="9" height="6" fill="#3f4043"/><path d="M0.5 2l4.5 3.5L9.5 2" stroke="#fdfdf8" fill="none"/></svg>
        sales@korvanevalves.example
      </li>
      <li><span class="contact-icon"></span>www.korvanevalves.example</li>
    </ul>

    <svg class="watermark" width="190" height="190" viewBox="0 0 190 190" aria-hidden="true">
      <circle cx="95" cy="95" r="95" fill="var(--watermark)"/>
    </svg>

    <p class="slogan">Made with Pride</p>
  </main>
</body>
</html>
```